Business Card Design For A Cajun Seafood Restaurant

We are opening a cajun seafood restaurant in a week. We mainly serve cajun seafood which is orginally from Louisiana. We want design on both sides of a business card. I have menu on the website. You can go to www.reednkettle.example to check out our menu.

Restaurant name: Reed N' Kettle
Phone: +1 (555) 304-7712
Address: 48206 Ludlow Row, #7, Bexmoor Flats, Ca90000
Email: reednkettle@mailbox.example
Website: www.reednkettle.example

Maybe add social media icons (facebook, instagram) if looks nice on the business card.
facebook.com/reednkettle
instagram.com/reednkettle or @reednkettle

Attached is the logo and other business card samples that I like.

```html
<!DOCTYPE html>
<html lang="en">
<head>
<meta charset="utf-8">
<title>Reed N' Kettle — Business Card</title>
<link rel="stylesheet" href="https://fonts.googleapis.com/css2?family=Roboto:wght@400;700&display=swap">
<style>
  :root {
    --stage: #3a3a3a;
    --card-white: #ffffff;
    --card-black: #0b0b0b;
    --orange: #f07a1a;
    --ink: #1a1a1a;
    --text-light: #f2f2f2;
  }
  * { box-sizing: border-box; margin: 0; padding: 0; }
  html, body { width: 1200px; height: 950px; overflow: hidden; }
  body {
    background: var(--stage);
    font-family: "Roboto", Arial, sans-serif;
    position: relative;
  }
  .card {
    position: absolute;
    left: 250px;
    width: 700px;
    height: 400px;
    overflow: hidden;
    background: var(--card-white);
    box-shadow: 0 12px 30px rgba(0,0,0,.45);
  }
  .card-front { top: 50px; }
  .card-back { top: 500px; }

  /* front */
  .brand {
    position: absolute;
    left: 0; right: 0; top: 0; bottom: 0;
    display: flex; align-items: center; justify-content: center;
    gap: 16px;
  }
  .brand-dot {
    width: 34px; height: 34px;
    border-radius: 50%;
    background: var(--orange);
    flex: none;
  }
  .brand-name {
    font-size: 38px;
    font-weight: 700;
    color: var(--ink);
  }

  /* back */
  .back-panel { position: absolute; inset: 0; width: 700px; height: 400px; }
  .contact {
    position: absolute;
    left: 50px; top: 150px;
    color: var(--text-light);
  }
  .contact-tick {
    position: absolute;
    left: -22px; top: 4px;
    width: 4px; height: 22px;
    background: var(--text-light);
  }
  .contact-name {
    font-size: 24px; font-weight: 700;
    color: var(--orange);
    text-transform: uppercase;
  }
  .contact-role { font-size: 17px; margin-top: 2px; }
  .contact-address { font-size: 15px; line-height: 1.35; margin-top: 16px; }
  .contact-list { list-style: none; margin-top: 10px; font-size: 15px; }
  .contact-list li { display: flex; align-items: center; gap: 8px; margin-top: 6px; }
  .contact-list svg { width: 15px; height: 15px; flex: none; }
  .social { display: flex; align-items: center; gap: 8px; }
  .social + .social { margin-left: 10px; }
  .social-mark { width: 13px; height: 13px; background: var(--orange); flex: none; }
</style>
</head>
<body>

<section class="card card-front">
  <div class="brand">
    <span class="brand-dot"></span>
    <span class="brand-name">Reed N' Kettle</span>
  </div>
</section>

<section class="card card-back">
  <svg class="back-panel" viewBox="0 0 700 400" preserveAspectRatio="none" aria-hidden="true">
    <path d="M0 0 H470 C380 120 400 260 520 400 H0 Z" fill="var(--card-black)"/>
  </svg>

  <div class="contact">
    <span class="contact-tick"></span>
    <div class="contact-name">Marla Quint</div>
    <div class="contact-role">President</div>
    <div class="contact-address">48206 Ludlow Row, #7<br>Bexmoor Flats, Ca90000</div>
    <ul class="contact-list">
      <li>
        <svg viewBox="0 0 16 16"><path fill="var(--orange)" d="M3 1h3l1.5 4-2 1.3a9 9 0 0 0 4.2 4.2L11 8.5l4 1.5v3a2 2 0 0 1-2 2A12 12 0 0 1 1 3a2 2 0 0 1 2-2z"/></svg>
        +1 (555) 304-7712
      </li>
      <li>
        <svg viewBox="0 0 16 16"><rect x="1" y="3" width="14" height="10" fill="var(--orange)"/><path d="M1 3l7 6 7-6" stroke="var(--card-black)" stroke-width="1.4" fill="none"/></svg>
        reednkettle@mailbox.example
      </li>
      <li>
        <svg viewBox="0 0 16 16"><circle cx="8" cy="8" r="7" fill="var(--orange)"/><path d="M1 8h14M8 1c-3 4-3 10 0 14M8 1c3 4 3 10 0 14" stroke="var(--card-black)" stroke-width="1.2" fill="none"/></svg>
        www.reednkettle.example
      </li>
      <li>
        <span class="social"><span class="social-mark"></span>reednkettle</span>
        <span class="social"><span class="social-mark"></span>@reednkettle</span>
      </li>
    </ul>
  </div>
</section>

</body>
</html>
```